Business Card Design Project - del varosi group

dear Sirs

we need business card design for our group ( DEL Varosi Group ) , i have got the Logo design of our group from pixel harbor in previous , so all need details relating to our group i think available with you, as well as the the chosen logo design

we hope to provide us with business card logo that to be appropaite and satisfactory to us .

thanks

note : logo design of our group is attached .
Updates

Reason: please extend the deadline of my project for additional 15 days because i didn't received appropriate design for our gruop yet . kindly beaware that i have received 77 design till now , supossed to send me 200-250 design at least . thanks

Target Market(s)

contents

name : Kerem EL Nadiri

position : Operation Manager

Industry/Entity Type

Business

Requirements
Must have

• person name

group logo
Nice to have
• logo color matching with back background

```html
<!DOCTYPE html>
<html lang="en">
<head>
<meta charset="utf-8">
<title>DEL Varosi Group – Business Card</title>
<link rel="stylesheet" href="https://fonts.googleapis.com/css2?family=Open+Sans:wght@400;600;700&display=swap">
<style>
  :root {
    --page: #e9e9ec;
    --card-white: #ffffff;
    --brand-blue: #0f5ea8;
    --brand-blue-deep: #0a4f93;
    --brand-blue-light: #1a73c6;
    --ink-white: #ffffff;
    --shadow: rgba(0, 0, 0, 0.18);
  }
  * { box-sizing: border-box; margin: 0; padding: 0; }
  html, body {
    width: 1200px; height: 758px; overflow: hidden;
    background: var(--page);
    font-family: "Open Sans", Arial, sans-serif;
  }
  .stage {
    position: relative; width: 1200px; height: 758px;
  }
  .card {
    position: absolute; top: 229px;
    width: 520px; height: 300px;
    border-radius: 26px;
    box-shadow: 0 8px 24px var(--shadow);
    overflow: hidden;
  }
  /* Front */
  .card--front { left: 40px; background: var(--card-white); }
  .front-logo {
    position: absolute; left: 44px; top: 122px; width: 210px;
    color: var(--brand-blue);
    font-weight: 700; font-size: 26px; letter-spacing: 0.5px;
    text-transform: uppercase; line-height: 1.1;
    white-space: nowrap;
  }
  .front-logo span { display: block; }
  .contact-panel {
    position: absolute; left: 270px; right: 0; top: 72px; height: 168px;
    background: var(--brand-blue);
    color: var(--ink-white);
  }
  .web-strip {
    position: absolute; left: 6px; top: 0; bottom: 0; width: 24px;
    border-left: 5px solid var(--brand-blue-light);
    display: flex; align-items: center; justify-content: center;
  }
  .web-strip span {
    transform: rotate(-90deg);
    white-space: nowrap; font-size: 11px; letter-spacing: 0.5px;
  }
  .contact-body { position: absolute; left: 44px; top: 10px; right: 12px; }
  .person-name { font-size: 16px; font-weight: 700; line-height: 1.2; }
  .person-role { font-size: 11px; margin-bottom: 10px; }
  .contact-list { list-style: none; font-size: 11px; line-height: 1.45; }
  .contact-list li { display: flex; align-items: center; gap: 5px; white-space: nowrap; }
  .contact-list svg { width: 9px; height: 9px; fill: var(--ink-white); flex: none; }
  .address { margin-top: 10px; font-size: 11px; line-height: 1.4; }
  /* Back */
  .card--back {
    left: 640px;
    background: linear-gradient(135deg, var(--brand-blue-deep), var(--brand-blue-light));
    color: var(--ink-white);
  }
  .back-logo {
    position: absolute; left: 0; right: 0; top: 100px; text-align: center;
    font-weight: 700; font-size: 40px; letter-spacing: 1px;
    text-transform: uppercase; line-height: 1; white-space: nowrap;
  }
  .back-web {
    position: absolute; left: 0; right: 0; top: 212px; text-align: center;
    font-size: 16px; letter-spacing: 1.5px;
  }
</style>
</head>
<body>
<main class="stage">
  <section class="card card--front" aria-label="Business card front">
    <div class="front-logo"><span>DEL Varosi</span><span>Group</span></div>
    <div class="contact-panel">
      <div class="web-strip"><span>www.website.com</span></div>
      <div class="contact-body">
        <div class="person-name">Kerem EL Nadiri</div>
        <div class="person-role">Operation Manager</div>
        <ul class="contact-list">
          <li><svg viewBox="0 0 10 10"><rect x="2.5" y="0.5" width="5" height="9" rx="1"/></svg>+1 555 014 2207</li>
          <li><svg viewBox="0 0 10 10"><path d="M2 0.5 L4 0.5 L4.8 3 L3.6 4 C4.2 5.4 4.9 6.1 6.2 6.6 L7.1 5.4 L9.5 6.2 L9.5 8.3 C9.5 9 9 9.5 8.3 9.5 C4.2 9.2 0.8 5.8 0.5 1.7 C0.5 1 1.2 0.5 2 0.5 Z"/></svg>+1 555 014 2208</li>
          <li><svg viewBox="0 0 10 10"><rect x="1" y="3" width="8" height="6" rx="1"/><rect x="3" y="0.5" width="4" height="3"/></svg>+1 555 014 2209</li>
          <li><svg viewBox="0 0 10 10"><rect x="0.5" y="2" width="9" height="6" rx="0.8"/></svg>name@harborinn.com</li>
        </ul>
        <div class="address">Street name, City<br>State, zip code</div>
      </div>
    </div>
  </section>

  <section class="card card--back" aria-label="Business card back">
    <div class="back-logo">DEL Varosi Group</div>
    <div class="back-web">www.website.com</div>
  </section>
</main>
</body>
</html>
```